Infoblatt
Zielgruppe
Talentförderung, Personalentwicklung, Beratung von Personalabteilungen
Zielgruppe: Personaler, HR Verantwortliche
Aufgabenstellung
Es geht um einen "One-Pager", der auf einem Kongress ausgelegt werden soll und in Kurzform einen Überblick über unser Unternehmen und unser Angebot informieren soll.
Wir haben Visitenkarten auf Recyclingpapier und möchten das Blatt konsistent auf das gleiche Papier drucken lassen, daher einfarbig schwarz. Format DIN A4 Hoch.
IDEE: Vom Stil wie eine Infografik aufbauen
TYPO: unser LOGO ist BEBAS NEUE und unsere Schrift Helvetica

```html
<!DOCTYPE html>
<html lang="de">
<head>
<meta charset="utf-8">
<title>KERNWERK – Infoblatt</title>
<link href="https://fonts.googleapis.com/css2?family=Arimo:wght@400;700&display=swap" rel="stylesheet">
<style>
  :root {
    --stage: #1b1b1b;
    --paper: #f4f4f4;
    --ink: #111111;
    --ink-soft: #3a3a3a;
    --rule: #222222;
    --photo-light: #e6e6e6;
    --photo-mid: #b9b9b9;
    --photo-dark: #8c8c8c;
    --portrait: #9a9a9a;
  }
  html, body {
    margin: 0;
    width: 1200px;
    height: 804px;
    overflow: hidden;
    background: var(--stage);
    font-family: "Arimo", "Helvetica Neue", Arial, sans-serif;
  }
  .sheet {
    position: absolute;
    left: 338px;
    top: 32px;
    width: 524px;
    height: 740px;
    background: var(--paper);
    overflow: hidden;
    color: var(--ink);
  }
  .sheet-photo {
    position: absolute;
    inset: 52px 0 0 0;
    background: linear-gradient(180deg, var(--photo-mid) 0%, var(--photo-light) 30%, var(--photo-mid) 55%, var(--photo-light) 80%, var(--photo-dark) 100%);
    opacity: 0.55;
  }
  .topics {
    position: absolute;
    top: 0;
    left: 0;
    right: 0;
    height: 52px;
    background: var(--paper);
    display: flex;
    justify-content: flex-end;
    gap: 26px;
    padding-right: 18px;
    align-items: flex-end;
  }
  .topic {
    font-size: 11px;
    line-height: 1.2;
    padding-bottom: 5px;
    border-bottom: 1px solid var(--rule);
    text-align: center;
    margin-bottom: 8px;
  }
  .team .portrait {
    position: absolute;
    width: 40px;
    height: 40px;
    border-radius: 50%;
    background: var(--portrait);
    border: 3px solid var(--paper);
    box-shadow: 0 0 0 1px var(--ink-soft);
  }
  .section-head {
    position: absolute;
    left: 0;
    width: 250px;
    height: 32px;
    border-bottom: 2px solid var(--rule);
  }
  .section-title {
    position: absolute;
    right: 6px;
    bottom: 2px;
    margin: 0;
    font-weight: 700;
    font-size: 28px;
    letter-spacing: 0.5px;
    line-height: 1;
    white-space: nowrap;
  }
  .section-text {
    position: absolute;
    left: 262px;
    width: 240px;
    font-size: 9px;
    line-height: 12px;
    color: var(--ink);
  }
  .section-text p { margin: 0 0 5px; }
  .section-text .lead { font-weight: 700; }
  .footer-photo {
    position: absolute;
    left: 0;
    top: 598px;
    width: 230px;
    height: 142px;
    background: radial-gradient(ellipse at 50% 40%, var(--photo-light) 0%, var(--photo-mid) 70%, var(--photo-dark) 100%);
  }
  .imprint {
    position: absolute;
    left: 26px;
    top: 612px;
    font-size: 9px;
    line-height: 1.35;
    color: var(--ink);
  }
  .brand {
    display: flex;
    align-items: center;
    gap: 6px;
    font-weight: 700;
    font-size: 15px;
    margin-bottom: 4px;
  }
  .brand-dot {
    width: 10px;
    height: 10px;
    background: var(--ink);
  }
</style>
</head>
<body>
<main class="sheet">
  <div class="sheet-photo" role="img" aria-label="Graustufenfoto eines hellen Büroraums als Hintergrund"></div>

  <nav class="topics">
    <div class="topic">Talentförderung</div>
    <div class="topic">Personalentwicklung</div>
    <div class="topic">Beratung für<br>Personalabteilungen</div>
  </nav>

  <div class="team">
    <div class="portrait" style="left:116px;top:150px" role="img" aria-label="Porträtfoto Teammitglied"></div>
    <div class="portrait" style="left:178px;top:100px" role="img" aria-label="Porträtfoto Teammitglied"></div>
    <div class="portrait" style="left:226px;top:148px" role="img" aria-label="Porträtfoto Teammitglied"></div>
    <div class="portrait" style="left:290px;top:102px" role="img" aria-label="Porträtfoto Teammitglied"></div>
    <div class="portrait" style="left:330px;top:152px" role="img" aria-label="Porträtfoto Teammitglied"></div>
    <div class="portrait" style="left:394px;top:100px" role="img" aria-label="Porträtfoto Teammitglied"></div>
  </div>

  <div class="section-head" style="top:270px"><h2 class="section-title">CREDO</h2></div>
  <div class="section-text" style="top:262px">
    <p class="lead">Woran wir glauben</p>
    <p>Wir glauben, dass sich persönliche und ökonomische Werte ergänzen – mehr noch, dass sie langfristig nicht ohne einander auskommen und dass sich emotionale Bindung als Mehrwert im Erfolg ausdrückt.</p>
  </div>

  <div class="section-head" style="top:360px"><h2 class="section-title">MEHRWERT</h2></div>
  <div class="section-text" style="top:360px">
    <p>Wir begleiten Menschen und Organisationen auf dem Weg in ihr Berufsleben.</p>
    <p>Für Unternehmen:<br>Talentförderung &amp; Talentmanagement<br>Professionalisierung der Personalarbeit<br>Organisationsberatung<br>Potentialorientierte Mitarbeiterführung</p>
    <p>Für die junge Generation:<br>Berufsorientierung<br>Bewerbungscoaching</p>
  </div>

  <div class="section-head" style="top:556px"><h2 class="section-title">MISSION</h2></div>
  <div class="section-text" style="top:560px">
    <p>VELMO hilft nicht, marktschreierisch anzupreisen, hinters Licht zu führen oder zu täuschen. VELMO hilft, Vertrauen zu schaffen. Wir legen großen Wert auf eine Beziehung, die Mandanten nicht Kunden entspricht. Für uns ist der partnerschaftliche Umgang mit Mandanten das Fundament. Wir haben keine Kunden, wir unterstützen Mandanten.</p>
  </div>

  <div class="footer-photo" role="img" aria-label="Graustufenfoto einer aufgerollten Papierrolle"></div>
  <div class="imprint">
    <div class="brand"><span class="brand-dot"></span>KERNWERK</div>
    Am Lindenhof 12, 10115 Berlin<br>
    Tel. 030 123 456 78<br>
    kontakt@kernwerk-beispiel.de<br>
    www.kernwerk-beispiel.de
  </div>
</main>
</body>
</html>
```